Awesome Business Card Design needed!

Hey there.
I'm looking for a simple but awesome business card design.
Type of company: Online advertisement agency
(please don't use the typical business people or statistics images on the card)
The front has to display the business name
and possibly some sort of logo ( perhaps something with the two M's of the biz name )
And the back of the card should say:
Name
Phone
Email
Let your imagination flow.
here are some designs that I like and that you can use as inspiration.
Simple but Awesome
http://images.lumavexo.com/designs/55128_877673_43091_thumbnail.jpg
http://images.lumavexo.com/designs/37714_747642_40106_image.jpg
http://images.lumavexo.com/designs/55128_877673_43091_image.jpg
http://images.lumavexo.com/designs/51321_781878_43091_image.jpg
http://images.lumavexo.com/designs/33378_399063_15912_image.jpg
http://images.lumavexo.com/designs/2337_271604_9495_image.jpg
good luck

```html
<!DOCTYPE html>
<html lang="en">
<head>
<meta charset="utf-8">
<title>Norvela Media – Business Card</title>
<link href="https://fonts.googleapis.com/css2?family=Michroma&display=swap" rel="stylesheet">
<style>
  :root {
    --stage: #e9eaec;
    --card-dark: #0d0e10;
    --card-mid: #1b1d21;
    --brand-blue: #4aa3e6;
    --silver: #c9ccd1;
    --silver-dim: #8d9197;
    --rule: #3a3d42;
  }
  * { box-sizing: border-box; margin: 0; padding: 0; }
  html, body {
    width: 1200px;
    height: 880px;
    overflow: hidden;
    background: var(--stage);
    font-family: "Michroma", "Arial Narrow", sans-serif;
  }
  .sheet {
    width: 1200px;
    height: 880px;
    display: flex;
    flex-direction: column;
    align-items: center;
    justify-content: center;
    gap: 48px;
  }
  .card {
    position: relative;
    width: 640px;
    height: 366px;
    border-radius: 4px;
    overflow: hidden;
    box-shadow: 0 10px 28px rgba(0,0,0,0.25);
  }
  .card-surface {
    position: absolute;
    inset: 0;
    background: linear-gradient(135deg, var(--card-mid) 0%, var(--card-dark) 60%, #070708 100%);
  }
  .card-content {
    position: relative;
    width: 100%;
    height: 100%;
  }

  /* Front */
  .card-front .card-content {
    display: flex;
    flex-direction: column;
    align-items: center;
    justify-content: center;
    gap: 28px;
  }
  .brand-square {
    width: 96px;
    height: 96px;
    background: linear-gradient(180deg, var(--brand-blue) 0%, var(--silver-dim) 100%);
  }
  .brand-name {
    font-size: 30px;
    letter-spacing: 1px;
    color: var(--silver);
    text-transform: uppercase;
  }

  /* Back */
  .card-back .card-content {
    display: flex;
    align-items: center;
    padding: 0 56px;
    gap: 44px;
  }
  .brand-block {
    display: flex;
    flex-direction: column;
    align-items: center;
    gap: 16px;
    width: 190px;
  }
  .brand-block .brand-square { width: 70px; height: 70px; }
  .brand-block .brand-name { font-size: 17px; text-align: center; }
  .contact {
    flex: 1;
    color: var(--silver);
    text-transform: uppercase;
  }
  .contact-name {
    font-size: 22px;
    letter-spacing: 1px;
    padding-bottom: 14px;
    border-bottom: 1px solid var(--rule);
    margin-bottom: 16px;
  }
  .contact-line {
    font-size: 13px;
    color: var(--silver-dim);
    margin-top: 10px;
  }
  .contact-line span { color: var(--silver); }
</style>
</head>
<body>
  <main class="sheet">
    <section class="card card-front">
      <div class="card-surface" role="img" aria-label="Dark card background with a faint repeating tile pattern"></div>
      <div class="card-content">
        <div class="brand-square"></div>
        <p class="brand-name">Norvela Media</p>
      </div>
    </section>

    <section class="card card-back">
      <div class="card-surface" role="img" aria-label="Dark card background with a faint repeating tile pattern"></div>
      <div class="card-content">
        <div class="brand-block">
          <div class="brand-square"></div>
          <p class="brand-name">Norvela Media</p>
        </div>
        <div class="contact">
          <p class="contact-name">Daniel Kessler</p>
          <p class="contact-line">P: <span>1221 555 0147</span></p>
          <p class="contact-line">E: <span>info@norvelamedia.com</span></p>
        </div>
      </div>
    </section>
  </main>
</body>
</html>
```